Graphic background for 10 Pull Up Banners

To produce a graphic background for a 100 cm wide by 200 cm high Pull-Up Display banner containing a Buddhist text in three languages: Tibetan, Mandarin and English. Please refer to uploaded file "Elements of Pull Up Banner". The design should be simple (not drawing attention away from the text). This design should then be varied for or extended to the next banner and so on until the 10th banner. When the banners are lined up, they should form a single design that is 1000 cm wide by 200 cm high.
An alternative way to look at the project is to produce a graphic background of 1000 cm width by 200 cm height that is then splitted into ten separate 100 cm wide by 200 cm high graphic to be used as background for 10 Buddhist texts (text 1, 2, 3, 4, 5, 6, 7, 8, 9a, 9b) on 10 Pull-Up Display Banners, the text in each banner being in the three languages mentioned earlier.
In either perspective, the design should be simple and not draw attention away from the texts. See uploaded PDF file "Examples.pdf"
Target Market(s)
For attendees at a Buddhist Event.
Look and feel
Each slider illustrates characteristics of the customer's brand and the style your logo design should communicate.

```html
<!DOCTYPE html>
<html lang="en">
<head>
<meta charset="utf-8">
<title>Mistakes to Avoid – Verse 6 Banner</title>
<link rel="stylesheet" href="https://fonts.googleapis.com/css2?family=Cormorant+Garamond:wght@600;700&family=Noto+Serif+Tibetan:wght@400;600&family=Noto+Sans+SC:wght@400;700&family=Open+Sans:wght@400;600&family=Arimo:wght@400&display=swap">
<style>
  :root {
    --banner-yellow: #f7ee1e;
    --banner-yellow-light: #fbf48a;
    --banner-gold: #c8a11c;
    --banner-gold-deep: #a57f12;
    --text-crimson: #a0142c;
    --text-red: #e8202a;
    --text-ink: #151515;
    --frame-white: #ffffff;
    --panel-veil: rgba(255, 255, 240, 0.28);
    --arrow-yellow: #f8f07a;
  }
  * { margin: 0; padding: 0; box-sizing: border-box; }
  html, body { width: 1200px; height: 1200px; overflow: hidden; background: #fff; }
  .sheet { position: relative; width: 1200px; height: 1200px; background: #fff; }

  /* Banner */
  .banner {
    position: absolute; left: 0; top: 0; width: 602px; height: 1200px; overflow: hidden;
    background:
      radial-gradient(ellipse 70% 40% at 55% 30%, var(--banner-yellow-light) 0%, rgba(251,244,138,0) 70%),
      linear-gradient(180deg, var(--banner-yellow) 0%, var(--banner-yellow) 62%, #e9d41c 80%, var(--banner-gold) 92%, var(--banner-gold-deep) 100%);
  }
  .banner-frame { position: absolute; left: 0; top: 0; }
  .deity-art {
    position: absolute; left: 84px; top: 54px; width: 120px; height: 140px; border-radius: 40% 40% 8px 8px;
    background: radial-gradient(ellipse at 50% 45%, #e9a31f 0%, #e7b92a 55%, rgba(240,220,40,0) 80%);
  }
  .title-small {
    position: absolute; left: 272px; top: 46px;
    font-family: "Cormorant Garamond", serif; font-weight: 700; font-size: 36px; letter-spacing: 3px;
    color: var(--text-crimson); line-height: 1;
  }
  .title-large {
    position: absolute; left: 238px; top: 72px;
    font-family: "Cormorant Garamond", serif; font-weight: 700; font-size: 100px; letter-spacing: 5px;
    color: var(--text-crimson); line-height: 1;
  }
  .title-chinese {
    position: absolute; left: 0; width: 734px; top: 162px; text-align: center;
    font-family: "Noto Sans SC", sans-serif; font-weight: 700; font-size: 27px; letter-spacing: 2px;
    color: var(--text-crimson);
  }
  .text-panel {
    position: absolute; left: 118px; width: 370px; height: 208px; background: var(--panel-veil);
    display: flex; flex-direction: column; justify-content: center; color: var(--text-crimson);
  }
  .panel-tibetan { top: 234px; align-items: center; font-family: "Noto Serif Tibetan", serif; font-size: 19px; line-height: 42px; }
  .panel-chinese { top: 476px; padding-left: 111px; font-family: "Noto Sans SC", sans-serif; font-size: 19px; line-height: 43px; }
  .panel-english { top: 722px; align-items: center; font-family: "Open Sans", sans-serif; font-size: 11.2px; line-height: 42.5px; }
  .dedication {
    position: absolute; left: 146px; top: 1016px; width: 320px; height: 124px;
    border: 2px solid rgba(255,255,255,0.35); background: rgba(255,255,230,0.18);
    display: flex; flex-direction: column; align-items: center; justify-content: center; gap: 6px;
    color: var(--text-crimson);
  }
  .dedication-tibetan { font-family: "Noto Serif Tibetan", serif; font-size: 12px; }
  .dedication-chinese { font-family: "Noto Sans SC", sans-serif; font-size: 14px; }
  .dedication-english { font-family: "Open Sans", sans-serif; font-size: 13px; color: #b8323c; }

  /* Reference column */
  .reference { position: absolute; left: 602px; top: 0; width: 598px; height: 1200px; text-align: center; }
  .verse-label { position: absolute; left: 0; right: 0; top: 152px; padding-left: 612px; margin-left: -602px;
    font-family: "Open Sans", sans-serif; font-size: 26px; color: var(--text-ink); }
  .ref-block { position: absolute; left: 306px; transform: translateX(-50%); white-space: nowrap; }
  .ref-verse { top: 152px; font-family: "Open Sans", sans-serif; font-size: 26px; color: var(--text-ink); }
  .ref-chinese { top: 190px; font-family: "Noto Sans SC", sans-serif; font-size: 31px; color: var(--text-red); }
  .ref-english { top: 240px; font-family: "Open Sans", sans-serif; font-size: 27px; color: var(--text-red); }
  .ref-tibetan { top: 326px; font-family: "Noto Serif Tibetan", serif; font-size: 27px; line-height: 59px; color: var(--text-ink); }
  .ref-arrow { position: absolute; left: 282px; top: 582px; }
  .ref-source { top: 706px; font-family: "Arimo", sans-serif; font-size: 52px; color: var(--text-crimson); }
</style>
</head>
<body>
<div class="sheet">
  <section class="banner">
    <svg class="banner-frame" width="602" height="1200" viewBox="0 0 602 1200">
      <path d="M86 14 H514 A70 70 0 0 0 584 84 V1116 A70 70 0 0 0 514 1186 H86 A70 70 0 0 0 18 1116 V84 A70 70 0 0 0 86 14 Z"
            fill="none" stroke="var(--frame-white)" stroke-width="2"/>
    </svg>
    <div class="deity-art" role="img" aria-label="Golden illustration of a seated deity on a lotus throne"></div>
    <div class="title-small">Mistakes to</div>
    <div class="title-large">Avoid</div>
    <div class="title-chinese">要避免的错误</div>

    <div class="text-panel panel-tibetan" lang="bo">
      <p>རྐང་པ་སྤོ་སའི་ལམ་མ་ནོར།།</p>
      <p>བློ་སེམས་གཏད་སའི་མི་མ་ནོར།།</p>
      <p>སྐྱབས་སུ་འགྲོ་སའི་མགོན་མ་ནོར།།</p>
      <p>སེམས་གཏམ་བཤད་སའི་གྲོགས་མ་ནོར།།</p>
    </div>
    <div class="text-panel panel-chinese" lang="zh">
      <p>足移动处路莫误。</p>
      <p>心交托处人莫误。</p>
      <p>所皈依处怙莫误。</p>
      <p>说心声处友莫误。</p>
    </div>
    <div class="text-panel panel-english">
      <p>Do not make the mistake of following the wrong path.</p>
      <p>Do not make the mistake of taking counsel from the wrong person.</p>
      <p>Do not make the mistake of seeking refuge in the wrong guide.</p>
      <p>Do not confide your thoughts to the wrong friend.</p>
    </div>
    <div class="dedication">
      <p class="dedication-tibetan" lang="bo">འགྲོ་བ་ཀུན་གྱིས་མཉམ་དུ་སངས་རྒྱས་ཐོབ་པར་ཤོག།</p>
      <p class="dedication-chinese" lang="zh">愿诸有情共证佛果位。</p>
      <p class="dedication-english">May all attain Buddhahood together.</p>
    </div>
  </section>

  <section class="reference">
    <p class="ref-block ref-verse">VERSE 6</p>
    <p class="ref-block ref-chinese" lang="zh">要避免的错误</p>
    <p class="ref-block ref-english">Mistakes To Avoid</p>
    <div class="ref-block ref-tibetan" lang="bo">
      <p>རྐང་པ་སྤོ་སའི་ལམ་མ་ནོར།།</p>
      <p>བློ་སེམས་གཏད་སའི་མི་མ་ནོར།།</p>
      <p>སྐྱབས་སུ་འགྲོ་སའི་མགོན་མ་ནོར།།</p>
      <p>སེམས་གཏམ་བཤད་སའི་གྲོགས་མ་ནོར།།</p>
    </div>
    <svg class="ref-arrow" width="40" height="124" viewBox="0 0 40 124">
      <polygon points="20,2 38,34 2,34" fill="var(--arrow-yellow)"/>
      <rect x="17.5" y="34" width="5" height="88" fill="var(--arrow-yellow)"/>
    </svg>
    <p class="ref-block ref-source">From PDF</p>
  </section>
</div>
</body>
</html>
```